PostCard Design Project

I am making a mailing postcard
I am having the mailing printed using 4 color foil on certain parts.
I am looking for a design that maximizes the foil process where certain parts are done in foil to grab the customers attention (example: if there is a car on the postcard the headlights would be done in foil) .
I am targeting some industries, (auto, real estate, medical, beauty) I would like the post card to have examples of postcard ideas for 2 or 3 of these industries.
specs:
the postcard should be atleast 6.5x9 up to 8.5x11, I don't want to restrict the space for the creative as I don't want everything to look like a huge mess. both sides will be used.
the piece is a direct mail piece so it has to meet requirements of https://www.mailvantor.com/business/pdf/quick-reference-guide.pdf
text will be
"business with no limits, meet mailing with no addresses, gain new customers through "Open Porch Route Drop" reach new customers at their home without needing their address. "
I also want some current print specials I am running included.
-double your order FREE (order 500 business cards and get 1000)
-250 100lb gloss stock brochures 99.00
-business packages (cards, envelopes and letterhead) 299
-1000 flyers 140.40
-5000 postcards 179.99
A list of services
banners
booklets
brochures
business cards
calendars
catalogs
CD/DVD packages
envelopes
event tickets
flyers
hangtags
postcards
posters
presentation folders
rack cards
labels
table tents
window cling and decal
"order 24/7 orders@inkwillow.com" must be included
my logo is InkWillow will be supplied later
ive received some great designs. however Im looking for something a little more modern like some zorvel would put out. if the amount of words is too much please feel free to edit. also an idea i had for the list of services i offer is to have it transparent yet readable as the background of the postcard some small some big but covering the entire backgroud. you can then design on top of that with other thing. just an early morning thought
Reason: I have uploaded a sketch of my idea, please take time to look at it for an accurate depiction of what im looking for. feel free to add elements that make it pop off the page
Reason: We are getting close i will be providing feed back today

```html
<!DOCTYPE html>
<html lang="en">
<head>
<meta charset="utf-8">
<title>InkWillow Postcard</title>
<link rel="stylesheet" href="https://fonts.googleapis.com/css2?family=Archivo+Black&family=Open+Sans:wght@400;600;700;800&display=swap">
<style>
  :root {
    --canvas: #ecebe8;
    --sky: #1aa3dd;
    --sky-deep: #0f86c0;
    --ink: #0b0b0b;
    --charcoal: #1c1c1c;
    --bar: #3a3a3a;
    --lime: #d6e23c;
    --cyan: #2fb0e6;
    --white: #ffffff;
    --soft: #bdbdbd;
  }
  * { margin: 0; padding: 0; box-sizing: border-box; }
  html, body { width: 1200px; height: 900px; overflow: hidden; }
  body { background: var(--canvas); position: relative; font-family: "Open Sans", sans-serif; }

  .card {
    position: absolute;
    top: 247px;
    width: 560px;
    height: 405px;
    overflow: hidden;
    box-shadow: 0 6px 18px rgba(0,0,0,.25);
  }
  .card--front { left: 20px; background: var(--sky); }
  .card--back { left: 620px; background: linear-gradient(160deg, var(--charcoal) 0%, var(--ink) 60%); }

  /* Front */
  .front__band {
    position: absolute; left: 0; right: 0; bottom: 0; height: 78px;
    background: var(--ink);
  }
  .front__brand {
    position: absolute; right: 22px; bottom: 22px;
    font-family: "Archivo Black", sans-serif; font-size: 30px; letter-spacing: 1px;
    color: var(--lime);
  }
  .headline {
    position: absolute; left: 22px; top: 40px;
    font-family: "Archivo Black", sans-serif; text-transform: uppercase;
    color: var(--white); font-size: 34px; line-height: 40px;
    text-shadow: 2px 3px 0 rgba(0,0,0,.55);
  }
  .headline .accent { color: var(--lime); }
  .headline .shine { font-size: 52px; line-height: 58px; }
  .front__hours {
    position: absolute; left: 22px; top: 262px;
    font-weight: 800; color: var(--white); font-size: 16px; line-height: 20px;
  }
  .front__email { font-size: 19px; }

  .sample { position: absolute; box-shadow: 0 3px 10px rgba(0,0,0,.4); }
  .sample--jewelry { left: 270px; top: 45px; width: 150px; height: 205px;
    background: linear-gradient(135deg, #5a5a5a, #1e1e1e 70%); }
  .sample--auto { left: 345px; top: 95px; width: 203px; height: 205px;
    background: linear-gradient(150deg, #f2f2f2 0 18%, #d41f26 18%, #a5121a 70%, #2a2a2a 100%); }
  .sample--beauty { left: 410px; top: 12px; width: 142px; height: 103px;
    background: linear-gradient(120deg, #f4f7fa, #e9c7ad 55%, #5aa4cf 100%); }

  /* Back */
  .services {
    position: absolute; left: 14px; top: 26px;
    list-style: none; color: var(--white); font-weight: 400;
    line-height: .98; letter-spacing: -.2px;
  }
  .services .is-cyan { color: var(--cyan); }
  .services .is-lime { color: var(--lime); }

  .back__brand {
    position: absolute; left: 205px; top: 58px;
    font-family: "Open Sans", sans-serif; font-weight: 800;
    font-size: 40px; letter-spacing: 1px; color: var(--lime);
  }
  .stamp-box {
    position: absolute; right: 22px; top: 22px; width: 80px; height: 50px;
    background: var(--white);
  }
  .specials {
    position: absolute; right: 14px; top: 118px; width: 240px;
    list-style: none; display: flex; flex-direction: column; align-items: flex-end; gap: 5px;
  }
  .specials li {
    background: var(--bar); color: var(--white);
    font-weight: 700; font-size: 10.5px; line-height: 14px;
    padding: 3px 8px; border-radius: 3px; text-align: center;
  }
  .address-box {
    position: absolute; right: 22px; top: 262px; width: 185px; height: 88px;
    background: var(--white);
  }
  .back__footer {
    position: absolute; left: 0; right: 0; bottom: 0; height: 28px;
    background: linear-gradient(90deg, transparent 30%, #4a4a4a 100%);
    color: var(--soft); font-size: 12px; line-height: 28px;
    text-align: right; padding-right: 16px;
  }
</style>
</head>
<body>

<section class="card card--front" aria-label="Postcard front">
  <div class="sample sample--jewelry" role="img" aria-label="Jewelry advertisement sample with silver rings on dark background"></div>
  <div class="sample sample--auto" role="img" aria-label="Auto advertisement sample with red sports car front"></div>
  <div class="sample sample--beauty" role="img" aria-label="Beauty advertisement sample with smiling model"></div>

  <h1 class="headline">
    Printing<br>
    That <span class="accent">Makes</span><br>
    Your<br>
    <span class="accent">Business</span><br>
    <span class="shine">Shine !</span>
  </h1>
  <p class="front__hours">24 hr/7 Day<br><span class="front__email">orders@inkwillow.com</span></p>

  <div class="front__band"></div>
  <div class="front__brand">INKWILLOW</div>
</section>

<section class="card card--back" aria-label="Postcard back">
  <ul class="services">
    <li class="is-cyan" style="font-size:11px">Banner</li>
    <li style="font-size:12px">booklets</li>
    <li style="font-size:13px">brochures</li>
    <li class="is-lime" style="font-size:12px">Buisness cards</li>
    <li style="font-size:20px">Calanders</li>
    <li style="font-size:22px">Catalougs</li>
    <li class="is-cyan" style="font-size:34px">Envelops</li>
    <li style="font-size:17px">Presentation Folder</li>
    <li class="is-lime" style="font-size:31px">Event Tickets</li>
    <li style="font-size:17px">Window cling and Decal</li>
    <li style="font-size:19px">CD/DVD Packages</li>
    <li class="is-lime" style="font-size:33px">rack Cards</li>
    <li style="font-size:29px">Table tents</li>
    <li class="is-cyan" style="font-size:37px">Flyers</li>
    <li style="font-size:17px">Hantags</li>
    <li class="is-lime" style="font-size:14px">postcard</li>
    <li style="font-size:12px">Posters</li>
  </ul>

  <div class="back__brand">INKWILLOW</div>
  <div class="stamp-box"></div>

  <ul class="specials">
    <li>Double your order FREE<br>(order 500 business cards and get 1000)</li>
    <li>250 100lb gloss stock brochures 99.00</li>
    <li>Business packages<br>(cards, envelopes and letterhead) 299</li>
    <li>1000 flyers 140.40</li>
    <li>5000 postcards 179.99</li>
  </ul>

  <div class="address-box"></div>
  <p class="back__footer">24 hr/7 Day orders@inkwillow.com</p>
</section>

</body>
</html>
```